Falkrin homes and renovations business card design.

Would like some new card designs utilizing my new logo that look professional. I am open to different colors on the logo or utilize the same ones we have. I like the original concept but would like to see some fresh ideas and build on what we have already done.

Target Market(s)

Custom home building industry, Real estate sales, Renovation projects.

Industry/Entity Type

Home Builder

Contact Information for Business Card

Falkrin Homes and Renovations
2871 96th Avenue
Frank, Alberta
T2R3W8
Home : 403- 718-4063 Cell: 403- 294-5170

My info is : Dax Falkrin, President and CEO
email: falkrinhomes@maildrop-example.net
Website: falkrinhomes-example.com
websit

Requirements
Must have
• Must Use my new logo design. I am open to different colors on the logo or utilize the same ones in the existing design. I can upload the original logo design if needed.

```html
<!DOCTYPE html>
<html lang="en">
<head>
<meta charset="utf-8">
<title>Falkrin Homes and Renovations – Business Card</title>
<link rel="stylesheet" href="https://fonts.googleapis.com/css2?family=Montserrat:wght@500;600&family=Oswald:wght@500&family=Open+Sans:wght@400;600&display=swap">
<style>
  :root {
    --backdrop: #e9e6e1;
    --card-black: #121212;
    --card-white: #ffffff;
    --gold: #b88a3c;
    --gold-light: #d3a851;
    --ink: #3a3a3a;
    --ink-soft: #6b6b6b;
    --rule: #c9c9c9;
  }
  * { box-sizing: border-box; margin: 0; padding: 0; }
  html, body {
    width: 1200px; height: 1000px; overflow: hidden;
    background: var(--backdrop);
  }
  .canvas {
    width: 1200px; height: 1000px;
    display: flex; flex-direction: column;
    align-items: center; justify-content: center; gap: 56px;
  }
  .card {
    width: 700px; height: 400px;
    position: relative;
    box-shadow: 0 10px 28px rgba(0,0,0,.18);
  }
  /* Front */
  .card--front {
    background: var(--card-black);
    display: flex; align-items: center; justify-content: center;
  }
  .brand {
    display: flex; align-items: center; gap: 14px;
    font-family: "Montserrat", sans-serif; font-weight: 600;
    color: var(--gold-light);
  }
  .brand__mark {
    width: 14px; height: 14px; background: var(--gold-light);
  }
  .brand__name { line-height: 1.1; }
  .brand__name .primary { display: block; font-size: 46px; letter-spacing: 2px; }
  .brand__name .secondary { display: block; font-size: 15px; letter-spacing: 2.4px; text-transform: uppercase; }
  /* Back */
  .card--back { background: var(--card-white); }
  .card--back .brand { position: absolute; left: 70px; top: 70px; color: var(--gold); }
  .card--back .brand__mark { background: var(--gold); width: 11px; height: 11px; }
  .card--back .brand__name .primary { font-size: 34px; }
  .card--back .brand__name .secondary { font-size: 11px; letter-spacing: 1.8px; }
  .person {
    position: absolute; left: 70px; top: 218px; text-align: right; width: 250px;
  }
  .person__name {
    font-family: "Oswald", sans-serif; font-weight: 500;
    font-size: 38px; letter-spacing: 1px; color: var(--ink); text-transform: uppercase;
  }
  .person__title {
    font-family: "Open Sans", sans-serif; font-weight: 600;
    font-size: 16px; color: var(--gold); margin-top: -2px;
  }
  .divider {
    position: absolute; left: 345px; top: 140px; width: 1px; height: 150px; background: var(--rule);
  }
  .contacts {
    position: absolute; left: 368px; top: 140px; list-style: none;
    font-family: "Open Sans", sans-serif; font-size: 16px; color: var(--ink-soft);
  }
  .contacts li { display: flex; align-items: center; gap: 12px; height: 36px; }
  .contacts svg { width: 16px; height: 16px; flex: none; }
  .contacts .accent { color: var(--gold); }
  .address {
    position: absolute; left: 0; right: 0; top: 330px;
    display: flex; justify-content: center; align-items: center; gap: 10px;
    font-family: "Open Sans", sans-serif; font-size: 16px; color: var(--ink-soft);
  }
  .address svg { width: 16px; height: 16px; }
</style>
</head>
<body>
<main class="canvas">
  <section class="card card--front" aria-label="Card front">
    <div class="brand">
      <span class="brand__mark"></span>
      <span class="brand__name">
        <span class="primary">FALKRIN</span>
        <span class="secondary">Homes and Renovations</span>
      </span>
    </div>
  </section>

  <section class="card card--back" aria-label="Card back">
    <div class="brand">
      <span class="brand__mark"></span>
      <span class="brand__name">
        <span class="primary">FALKRIN</span>
        <span class="secondary">Homes and Renovations</span>
      </span>
    </div>

    <div class="person">
      <h1 class="person__name">Dax Falkrin</h1>
      <p class="person__title">President and CEO</p>
    </div>

    <div class="divider"></div>

    <ul class="contacts">
      <li>
        <svg viewBox="0 0 16 16" fill="none" stroke="#b88a3c" stroke-width="1.6" stroke-linecap="round"><path d="M3 2.5l2.5-.5 1.5 3-1.6 1.2a8 8 0 0 0 4.4 4.4L11 9l3 1.5-.5 2.5c-6 .5-11-4.5-10.5-10.5z"/></svg>
        <span>403 718 4063</span>
      </li>
      <li>
        <svg viewBox="0 0 16 16" fill="none" stroke="#b88a3c" stroke-width="1.6"><rect x="4" y="1.5" width="8" height="13" rx="1.5"/><line x1="7" y1="12" x2="9" y2="12"/></svg>
        <span>403 294 5170</span>
      </li>
      <li>
        <svg viewBox="0 0 16 16" fill="none" stroke="#b88a3c" stroke-width="1.6"><rect x="1.5" y="3.5" width="13" height="9" rx="1"/><path d="M1.5 4l6.5 5 6.5-5"/></svg>
        <span>falkrinhomes@maildrop-example.net</span>
      </li>
      <li>
        <svg viewBox="0 0 16 16" fill="none" stroke="#b88a3c" stroke-width="1.6"><circle cx="8" cy="8" r="6.5"/><path d="M1.5 8h13M8 1.5c2.5 3 2.5 10 0 13M8 1.5c-2.5 3-2.5 10 0 13"/></svg>
        <span>www.<span class="accent">falkrinhomes-example.com</span></span>
      </li>
    </ul>

    <p class="address">
      <svg viewBox="0 0 16 16" fill="none" stroke="#b88a3c" stroke-width="1.6" stroke-linejoin="round"><path d="M14.5 1.5L1.5 7l5.5 2 2 5.5z"/></svg>
      <span>2871 96th Avenue Frank, Alberta</span>
    </p>
  </section>
</main>
</body>
</html>
```